Website Design for The Elder Nook

Please design and code a new website.
Here are the sites I like best:
http://www.voyaglint.com/alternate/
http://www.wheelgiftbay.org
Please make it similar but look at the competitor site (below) for images and wording. This is NOT a car donation site. It's a senior lead placement site like https://www.kinhavenfinder.com. I just like this sites above as a lead generation sites.
Competitor site:
https://www.kinhavenfinder.com (use ideas / verbiage from this site)
Updates
Competitor site:
Coding
Coded - Design and coding required
Number of Pages Required
1 page
Look and feel
Each slider illustrates characteristics of the customer's brand and the style your logo design should communicate.

```html
<!DOCTYPE html>
<html lang="en">
<head>
<meta charset="utf-8">
<title>The Elder Nook – Find Senior Living Near You</title>
<link href="https://fonts.googleapis.com/css2?family=Montserrat:wght@500;600;700;800&family=Open+Sans:wght@400;600;700&display=swap" rel="stylesheet">
<style>
:root{
  --navy:#0c3a68;
  --navy-deep:#082c52;
  --blue:#2e6597;
  --blue-soft:#4f80ad;
  --teal:#1fb3a3;
  --teal-dark:#14958a;
  --ink:#2b2f36;
  --muted:#5c636d;
  --line:#d9dee5;
  --white:#ffffff;
  --paper:#f4f6f8;
}
*{box-sizing:border-box;margin:0;padding:0}
html,body{width:1200px;height:5114px;overflow:hidden}
body{font-family:"Open Sans",Arial,sans-serif;color:var(--ink);background:var(--white);font-size:15px;line-height:1.5}
h1,h2,h3,h4{font-family:"Montserrat",Arial,sans-serif}
section,header,footer,nav{position:relative;width:1200px;overflow:hidden}
.accent{color:var(--teal)}
.btn{display:inline-block;background:var(--teal);color:var(--white);font-weight:700;font-family:"Montserrat",Arial,sans-serif;border-radius:3px;padding:10px 26px;font-size:15px}
.photo{display:block}

/* header */
.site-header{height:126px;display:flex;align-items:center;justify-content:space-between;padding:0 40px}
.brand{display:flex;align-items:center;gap:12px}
.brand-dot{width:38px;height:38px;border-radius:50%;background:var(--teal)}
.brand-name{font-family:"Montserrat",Arial,sans-serif;font-weight:700;font-size:30px;color:var(--navy);line-height:1}
.brand-tag{font-size:11px;color:var(--muted);letter-spacing:.5px;margin-top:4px}
.header-phone{display:flex;align-items:center;gap:12px}
.phone-icon{width:44px;height:44px;border-radius:50%;background:var(--navy);display:flex;align-items:center;justify-content:center}
.phone-num{font-family:"Montserrat",Arial,sans-serif;font-weight:800;font-size:28px;color:var(--navy);line-height:1}
.phone-sub{font-size:12px;color:var(--muted)}

.main-nav{height:44px;background:var(--navy);display:flex;justify-content:center;align-items:center;gap:34px}
.main-nav a{color:var(--white);font-family:"Montserrat",Arial,sans-serif;font-weight:700;font-size:13px;text-transform:uppercase;text-decoration:none}

/* hero */
.hero{height:493px}
.hero-photo{position:absolute;inset:0;background:linear-gradient(180deg,#9cb7c9 0%,#b7c6a2 45%,#6f8f4e 100%)}
.hero-title{position:absolute;left:150px;top:170px;color:var(--white);font-size:38px;font-weight:700;line-height:1.22;text-align:center;text-shadow:0 2px 6px rgba(0,0,0,.35)}
.lead-form{position:absolute;right:70px;top:72px;width:380px;background:rgba(255,255,255,.92);box-shadow:0 4px 18px rgba(0,0,0,.2)}
.lead-form h3{background:var(--teal);color:var(--white);text-align:center;font-size:20px;padding:10px 0}
.form-body{padding:16px 16px 18px;display:grid;grid-template-columns:1fr 1fr;gap:10px}
.field{border:1px solid var(--line);background:var(--white);height:44px;padding:0 12px;display:flex;align-items:center;font-size:13px;font-weight:600;color:var(--ink)}
.field.wide{grid-column:1/3}
.field.select{justify-content:space-between}
.lead-form .btn{width:130px;text-align:center;padding:10px 0}

/* support band */
.support{height:170px;background:var(--white);display:flex}
.support-lead{width:440px;background:var(--navy);color:var(--white);padding:40px 0 0 30px;clip-path:polygon(0 0,100% 0,88% 100%,0 100%)}
.support-lead h2{font-size:30px;line-height:1.15;font-weight:800;text-transform:uppercase}
.support-lead h2 span{font-size:40px;display:block}
.support-items{display:flex;flex:1;justify-content:space-around;align-items:center;padding:0 20px 0 10px}
.support-item{width:120px;text-align:center;font-size:12px;font-weight:700;color:var(--navy);line-height:1.3}
.support-item svg{display:block;margin:0 auto 10px}

/* how it works */
.how{height:637px;padding-top:110px}
.section-title{text-align:center;font-size:34px;font-weight:700;color:var(--navy)}
.steps{display:flex;gap:30px;padding:40px 50px 0}
.step{width:255px}
.step h4{font-size:15px;font-weight:700;color:var(--ink);margin-bottom:12px}
.step .photo{height:170px;margin-bottom:16px}
.step p{font-size:15px;color:var(--muted);line-height:1.55}

/* no cost */
.no-cost{height:470px;background:linear-gradient(120deg,#245785 0%,#3a6f9f 60%,#5c88b0 100%);text-align:center;color:var(--white);padding-top:150px}
.no-cost h2{font-size:48px;font-weight:700}
.no-cost p{font-size:21px;font-weight:600;margin-top:24px;line-height:1.4}
.no-cost .call{font-family:"Montserrat",Arial,sans-serif;font-size:32px;font-weight:700;color:var(--teal);margin-top:34px}

/* veterans */
.veterans{height:420px;padding:105px 70px 0}
.veterans h2{font-size:30px;color:var(--navy);font-weight:700}
.veterans p{width:680px;margin-top:28px;font-size:18px;color:var(--muted);line-height:1.55}
.veterans .btn{margin-top:26px}
.vet-photo{position:absolute;right:110px;top:90px;width:250px;height:250px;border-radius:50%;border:6px solid var(--white);box-shadow:0 4px 16px rgba(0,0,0,.2);background:linear-gradient(135deg,#c8d3de,#7f98b2 60%,#b23a3a)}

/* testimonials */
.testimonials{height:510px;background:linear-gradient(180deg,#2d5f8e,#3d72a3);padding-top:100px;color:var(--white)}
.testimonials h2{text-align:center;font-size:30px;font-weight:700}
.quotes{display:flex;gap:40px;justify-content:center;margin-top:50px}
.quote{width:340px}
.quote-text{display:flex;gap:8px;font-size:14px;line-height:1.5}
.qmark{font-family:"Montserrat",Arial,sans-serif;font-size:60px;line-height:.8;color:var(--teal);font-weight:800}
.quote-meta{display:flex;align-items:center;justify-content:space-between;margin-top:16px;padding-left:8px}
.quote-name{font-style:italic;font-weight:600;font-size:15px}
.avatar{width:80px;height:80px;border-radius:50%;border:4px solid var(--white);background:linear-gradient(135deg,#e3c9b4,#a98a76)}
.dots{display:flex;justify-content:center;gap:8px;margin-top:32px}
.dots span{width:11px;height:11px;border-radius:50%;border:1px solid var(--white)}
.dots span.on{background:var(--white)}

/* states */
.states{height:650px;padding-top:90px}
.states-body{display:flex;gap:70px;padding:60px 80px 0}
.care-tabs{width:270px;display:flex;flex-direction:column;gap:12px}
.care-tab{height:52px;display:flex;align-items:center;gap:14px;border:1px solid var(--line);font-weight:700;font-size:16px;color:var(--ink);padding-right:14px;justify-content:flex-start}
.care-tab i{width:52px;height:52px;background:var(--navy);display:flex;align-items:center;justify-content:center;margin:-1px 0 -1px -1px}
.care-tab.on{color:var(--teal);border-color:var(--teal)}
.care-tab.on i{background:var(--teal)}
.care-tab.on b{margin-left:auto;color:var(--teal)}
.state-cols{display:flex;gap:70px;font-size:15px;line-height:1.55;color:var(--ink)}
.state-cols ul{list-style:none;width:170px}

/* advisor */
.advisor{height:570px;background:linear-gradient(110deg,#163f68 0%,#2d5f8e 55%,#a8c3d9 100%);color:var(--white);padding:150px 0 0 80px}
.advisor h2{font-size:34px;font-weight:700;line-height:1.2}
.advisor .lede{font-size:17px;font-weight:600;margin-top:26px;width:540px}
.advisor ul{list-style:none;margin-top:24px}
.advisor li{display:flex;align-items:center;gap:16px;font-weight:600;font-size:16px;margin-bottom:18px}

/* city lists */
.cities{height:650px;display:flex;gap:80px;padding:70px 80px 0}
.city-col{width:320px}
.city-col h3{font-size:22px;font-weight:700;color:var(--navy);margin-bottom:16px}
.city-col ul{list-style:none;font-size:14.5px;line-height:1.6;color:var(--ink)}

/* footer */
.site-footer{height:326px;background:var(--paper)}
.footer-photo{position:absolute;left:0;bottom:0;width:250px;height:300px;background:linear-gradient(180deg,#c9ccd1,#8b8f96)}
.footer-about{position:absolute;left:290px;top:80px;width:330px}
.footer-about h4,.footer-links h4{font-size:14px;font-weight:800;color:var(--navy);text-transform:uppercase;margin-bottom:12px}
.footer-about p{font-size:13px;color:var(--muted);line-height:1.55}
.footer-links{position:absolute;left:650px;top:80px}
.footer-links ul{list-style:none;font-size:13px;line-height:1.6;color:var(--muted)}
.footer-brand{position:absolute;right:0;top:0;width:390px;height:326px;background:var(--navy);color:var(--white);padding:70px 0 0 90px;clip-path:polygon(18% 0,100% 0,100% 100%,0 100%)}
.footer-brand .brand-name{color:var(--white);font-size:28px}
.footer-brand .brand-tag{color:#c4d3e3}
.footer-brand .header-phone{margin-top:40px}
.footer-brand .phone-icon{background:var(--white)}
.footer-brand .phone-num{color:var(--white);font-size:24px}
.footer-brand .phone-sub{color:#c4d3e3}
.copyright{height:48px;background:var(--white);display:flex;align-items:center;justify-content:space-between;padding:0 30px;font-size:12px;font-weight:700;color:var(--navy)}
.social{display:flex;gap:8px}
.social span{width:20px;height:20px;border-radius:50%;background:var(--navy)}
</style>
</head>
<body>

<header class="site-header">
  <div class="brand">
    <span class="brand-dot"></span>
    <div>
      <div class="brand-name">The Elder Nook</div>
      <div class="brand-tag">CONNECTING FAMILIES TO SENIOR LIVING</div>
    </div>
  </div>
  <div class="header-phone">
    <span class="phone-icon"><svg width="22" height="22" viewBox="0 0 24 24"><path fill="#fff" d="M6.6 10.8a15 15 0 0 0 6.6 6.6l2.2-2.2c.3-.3.7-.4 1-.2 1.1.4 2.3.6 3.6.6.6 0 1 .4 1 1V20c0 .6-.4 1-1 1A17 17 0 0 1 3 4c0-.6.4-1 1-1h3.5c.6 0 1 .4 1 1 0 1.3.2 2.5.6 3.6.1.3 0 .7-.2 1z"/></svg></span>
    <div>
      <div class="phone-num">1-800-555-0142</div>
      <div class="phone-sub">Talk Today to a Local Advisor for FREE</div>
    </div>
  </div>
</header>

<nav class="main-nav">
  <a>Assisted Living</a><a>Memory Care</a><a>Nursing Homes</a><a>More Living Options ▾</a><a>Planning &amp; Advice</a>
</nav>

<section class="hero">
  <div class="hero-photo photo" role="img" aria-label="Senior couple walking together on a lawn beside a person in a wheelchair"></div>
  <h1 class="hero-title">You know your family.<br>We know Senior Living.<br>Find Senior Living Near You.</h1>
  <form class="lead-form">
    <h3>Contact us now!</h3>
    <div class="form-body">
      <div class="field">First Name*</div>
      <div class="field">Last Name*</div>
      <div class="field">Primary Phone*</div>
      <div class="field">Cell Phone*</div>
      <div class="field wide">Email Address*</div>
      <div class="field wide select">State* <span>▾</span></div>
      <div><span class="btn">SUBMIT</span></div>
    </div>
  </form>
</section>

<section class="support">
  <div class="support-lead">
    <h2>The support you<br>need to make the<span>right choice</span></h2>
  </div>
  <div class="support-items">
    <div class="support-item"><svg width="54" height="54" viewBox="0 0 54 54"><circle cx="27" cy="18" r="9" fill="#1fb3a3"/><path d="M10 48c0-10 8-16 17-16s17 6 17 16z" fill="#0c3a68"/></svg>Dedicated local advisor</div>
    <div class="support-item"><svg width="54" height="54" viewBox="0 0 54 54"><rect x="8" y="20" width="22" height="28" fill="#0c3a68"/><rect x="30" y="10" width="16" height="38" fill="#1fb3a3"/><rect x="14" y="26" width="5" height="5" fill="#fff"/><rect x="21" y="26" width="5" height="5" fill="#fff"/><rect x="35" y="16" width="6" height="6" fill="#fff"/></svg>Hand-picked list of communities to match your needs</div>
    <div class="support-item"><svg width="54" height="54" viewBox="0 0 54 54"><rect x="12" y="6" width="30" height="42" rx="2" fill="#0c3a68"/><rect x="18" y="14" width="18" height="3" fill="#fff"/><rect x="18" y="22" width="18" height="3" fill="#fff"/><rect x="18" y="30" width="12" height="3" fill="#fff"/><circle cx="38" cy="42" r="8" fill="#1fb3a3"/></svg>Full details and pricing</div>
    <div class="support-item"><svg width="54" height="54" viewBox="0 0 54 54"><rect x="8" y="12" width="38" height="34" rx="2" fill="#0c3a68"/><rect x="8" y="12" width="38" height="8" fill="#1fb3a3"/><g fill="#fff"><rect x="14" y="25" width="6" height="5"/><rect x="24" y="25" width="6" height="5"/><rect x="34" y="25" width="6" height="5"/><rect x="14" y="34" width="6" height="5"/><rect x="24" y="34" width="6" height="5"/></g></svg>Help scheduling tours</div>
    <div class="support-item"><svg width="54" height="54" viewBox="0 0 54 54"><path d="M8 26 27 10l19 16v22H8z" fill="#0c3a68"/><rect x="22" y="34" width="10" height="14" fill="#1fb3a3"/></svg>Move-in support</div>
  </div>
</section>

<section class="how">
  <h2 class="section-title">How our <span class="accent">service works</span></h2>
  <div class="steps">
    <div class="step">
      <h4>01. Talk with your local advisor</h4>
      <div class="photo" role="img" aria-label="Advisor wearing a headset on a call" style="background:linear-gradient(135deg,#dfe7ee,#a8b9c9)"></div>
      <p>Call us to get connected to your local Senior Living Advisor, who will do an assessment of you or your loved one's lifestyle, care needs, budget, and preferences for senior living.</p>
    </div>
    <div class="step">
      <h4>02. Get information on care options</h4>
      <div class="photo" role="img" aria-label="Advisor reviewing care options with a senior couple" style="background:linear-gradient(135deg,#e9ddd0,#b59c86)"></div>
      <p>Based on your assessment, your Advisor will send you information on senior living communities tailored to your needs, saving you the time trying to find the right ones to evaluate.</p>
    </div>
    <div class="step">
      <h4>03. Choose communities to visit</h4>
      <div class="photo" role="img" aria-label="Family touring a senior living community" style="background:linear-gradient(135deg,#d7dccb,#8f9c7a)"></div>
      <p>Have tours scheduled for you, get tips on looking for the right fit for your needs, and consult with your Advisor at any time - all at no cost to you.</p>
    </div>
    <div class="step">
      <h4>04. Transition to new home</h4>
      <div class="photo" role="img" aria-label="Seniors settling into their new home" style="background:linear-gradient(135deg,#e6d8cc,#a48b7b)"></div>
      <p>When you've selected the right living arrangement, get guidance on making the move as smooth as possible.</p>
    </div>
  </div>
</section>

<section class="no-cost" role="img" aria-label="Blue-tinted photo of seniors in a community lounge">
  <h2>There's No Cost to You</h2>
  <p>We work with over 20,000 senior living communities.<br>Our community partners pay us for placement services.</p>
  <div class="call">Call 800-555-0142</div>
</section>

<section class="veterans">
  <h2>Access up to $2,000 per month <span class="accent">in veteran's aid</span></h2>
  <p>We work with Veterans every day. Most veteran families do not know of a key benefit available to them and their families. It's called the Veteran's Aid and Attendance benefit. This benefit can help pay for senior living and home care.</p>
  <span class="btn">Learn More</span>
  <div class="vet-photo photo" role="img" aria-label="Veteran saluting in front of a flag"></div>
</section>

<section class="testimonials">
  <h2>97% of our customers recommend our service</h2>
  <div class="quotes">
    <div class="quote">
      <div class="quote-text"><span class="qmark">“</span><p>Our advisor listened closely and found Mom a warm place near us. The whole search felt calm, quick and kind from start to finish.</p></div>
      <div class="quote-meta"><span class="quote-name">Martha Ellison</span><span class="avatar" role="img" aria-label="Customer portrait"></span></div>
    </div>
    <div class="quote">
      <div class="quote-text"><span class="qmark">“</span><p>We toured three lovely homes in one week. Dad chose the one with a garden, and he is happier than he has been in years.</p></div>
      <div class="quote-meta"><span class="quote-name">Clara Deane</span><span class="avatar" role="img" aria-label="Customer portrait"></span></div>
    </div>
    <div class="quote">
      <div class="quote-text"><span class="qmark">“</span><p>Clear pricing, honest advice and no pressure at all. I would tell any family facing this choice to give them a call first.</p></div>
      <div class="quote-meta"><span class="quote-name">Jonathan Hale</span><span class="avatar" role="img" aria-label="Customer portrait"></span></div>
    </div>
  </div>
  <div class="dots"><span class="on"></span><span></span><span></span><span></span></div>
</section>

<section class="states">
  <h2 class="section-title">Senior living <span class="accent">by state</span></h2>
  <div class="states-body">
    <div class="care-tabs">
      <div class="care-tab on"><i><svg width="22" height="22" viewBox="0 0 24 24"><circle cx="12" cy="6" r="4" fill="#fff"/><path d="M4 22c0-6 4-9 8-9s8 3 8 9z" fill="#fff"/></svg></i>Assisted Living<b>◀</b></div>
      <div class="care-tab"><i><svg width="22" height="22" viewBox="0 0 24 24"><circle cx="12" cy="12" r="8" fill="none" stroke="#fff" stroke-width="3"/></svg></i>Memory Care</div>
      <div class="care-tab"><i><svg width="22" height="22" viewBox="0 0 24 24"><circle cx="12" cy="6" r="4" fill="#fff"/><rect x="8" y="11" width="8" height="11" fill="#fff"/></svg></i>Independent Living</div>
      <div class="care-tab"><i><svg width="22" height="22" viewBox="0 0 24 24"><rect x="4" y="10" width="16" height="10" fill="#fff"/><rect x="10" y="3" width="4" height="8" fill="#fff"/></svg></i>Nursing Home</div>
      <div class="care-tab"><i><svg width="22" height="22" viewBox="0 0 24 24"><path d="M3 12 12 4l9 8v9H3z" fill="#fff"/></svg></i>Care Homes</div>
    </div>
    <div class="state-cols">
      <ul><li>Alabama</li><li>Arizona</li><li>Arkansas</li><li>California</li><li>Colorado</li><li>Connecticut</li><li>Delaware</li><li>District of Columbia</li><li>Florida</li><li>Georgia</li><li>Hawaii</li><li>Idaho</li><li>Illinois</li><li>Indiana</li><li>Iowa</li><li>Kansas</li><li>Kentucky</li></ul>
      <ul><li>Louisiana</li><li>Maine</li><li>Maryland</li><li>Massachusetts</li><li>Michigan</li><li>Minnesota</li><li>Mississippi</li><li>Missouri</li><li>Montana</li><li>Nebraska</li><li>Nevada</li><li>New Hampshire</li><li>New Jersey</li><li>New Mexico</li><li>New York</li><li>North Carolina</li><li>North Dakota</li></ul>
      <ul><li>Ohio</li><li>Oklahoma</li><li>Oregon</li><li>Pennsylvania</li><li>Rhode Island</li><li>South Carolina</li><li>South Dakota</li><li>Tennessee</li><li>Texas</li><li>Utah</li><li>Vermont</li><li>Virginia</li><li>Washington</li><li>West Virginia</li><li>Wisconsin</li><li>Wyoming</li></ul>
    </div>
  </div>
</section>

<section class="advisor" role="img" aria-label="Senior raising arms joyfully in a bright window, tinted blue">
  <h2>Your local advisor.<br>You decide.</h2>
  <p class="lede">Over 400 senior advisors across the U.S. and Canada are ready to help your family with:</p>
  <ul>
    <li><svg width="24" height="24" viewBox="0 0 24 24"><path d="M12 2a7 7 0 0 0-7 7c0 5 7 13 7 13s7-8 7-13a7 7 0 0 0-7-7z" fill="#1fb3a3"/><circle cx="12" cy="9" r="2.5" fill="#fff"/></svg>Insider's tips for the area near you</li>
    <li><svg width="24" height="24" viewBox="0 0 24 24"><path d="M4 4h16v11H9l-5 4z" fill="#1fb3a3"/></svg>Advice tailored to your unique situation</li>
    <li><svg width="24" height="24" viewBox="0 0 24 24"><circle cx="12" cy="12" r="9" fill="none" stroke="#1fb3a3" stroke-width="2.5"/><path d="M12 7v5l3 2" stroke="#1fb3a3" stroke-width="2.5" fill="none"/></svg>Time saving know-how and resources</li>
  </ul>
</section>

<section class="cities">
  <div class="city-col">
    <h3>Independent living</h3>
    <ul><li>New York Independent Living</li><li>Los Angeles Independent Living</li><li>Chicago Independent Living</li><li>Dallas Independent Living</li><li>Houston Independent Living</li><li>Washington DC Independent Living</li><li>Philadelphia Independent Living</li><li>Miami Independent Living</li><li>Atlanta Independent Living</li><li>Boston Independent Living</li><li>San Francisco Independent Living</li><li>Phoenix Independent Living</li><li>Orange County Independent Living</li><li>Detroit Independent Living</li><li>Seattle Independent Living</li><li>Minneapolis Independent Living</li><li>San Diego Independent Living</li><li>Tampa Independent Living</li><li>Denver Independent Living</li><li>St. Louis Independent Living</li><li>Baltimore Independent Living</li></ul>
  </div>
  <div class="city-col">
    <h3>Memory <span class="accent">care</span></h3>
    <ul><li>New York Memory Care</li><li>Los Angeles Memory Care</li><li>Chicago Memory Care</li><li>Dallas Memory Care</li><li>Houston Memory Care</li><li>Washington DC Memory Care</li><li>Philadelphia Memory Care</li><li>Miami Memory Care</li><li>Atlanta Memory Care</li><li>Boston Memory Care</li><li>San Francisco Memory Care</li><li>Phoenix Memory Care</li><li>Orange County Memory Care</li><li>Detroit Memory Care</li><li>Seattle Memory Care</li><li>Minneapolis Memory Care</li><li>San Diego Memory Care</li><li>Tampa Memory Care</li><li>Denver Memory Care</li><li>St. Louis Memory Care</li><li>Baltimore Memory Care</li></ul>
  </div>
  <div class="city-col">
    <h3>Nursing <span class="accent">homes</span></h3>
    <ul><li>New York Nursing Homes</li><li>Los Angeles Nursing Homes</li><li>Chicago Nursing Homes</li><li>Dallas Nursing Homes</li><li>Houston Nursing Homes</li><li>Washington DC Nursing Homes</li><li>Philadelphia Nursing Homes</li><li>Miami Nursing Homes</li><li>Atlanta Nursing Homes</li><li>Boston Nursing Homes</li><li>San Francisco Nursing Homes</li><li>Phoenix Nursing Homes</li><li>Orange County Nursing Homes</li><li>Detroit Nursing Homes</li><li>Seattle Nursing Homes</li><li>Minneapolis Nursing Homes</li><li>San Diego Nursing Homes</li><li>Tampa Nursing Homes</li><li>Denver Nursing Homes</li><li>St. Louis Nursing Homes</li><li>Baltimore Nursing Homes</li></ul>
  </div>
</section>

<footer class="site-footer">
  <div class="footer-photo photo" role="img" aria-label="Smiling senior man in a cardigan"></div>
  <div class="footer-about">
    <h4>About The Elder Nook</h4>
    <p>We help families compare senior living options with free, local guidance. Our advisors listen, share honest pricing and arrange tours, so every family can choose a caring new home with confidence and peace of mind.</p>
  </div>
  <div class="footer-links">
    <h4>Quick Links</h4>
    <ul><li>Assisted Living</li><li>Memory Care</li><li>Nursing Home</li><li>More Living Options</li><li>Planning &amp; Advice</li><li>How Our Service Works</li></ul>
  </div>
  <div class="footer-brand">
    <div class="brand">
      <span class="brand-dot"></span>
      <div>
        <div class="brand-name">The Elder Nook</div>
        <div class="brand-tag">CONNECTING FAMILIES TO SENIOR LIVING</div>
      </div>
    </div>
    <div class="header-phone">
      <span class="phone-icon"><svg width="22" height="22" viewBox="0 0 24 24"><path fill="#0c3a68" d="M6.6 10.8a15 15 0 0 0 6.6 6.6l2.2-2.2c.3-.3.7-.4 1-.2 1.1.4 2.3.6 3.6.6.6 0 1 .4 1 1V20c0 .6-.4 1-1 1A17 17 0 0 1 3 4c0-.6.4-1 1-1h3.5c.6 0 1 .4 1 1 0 1.3.2 2.5.6 3.6.1.3 0 .7-.2 1z"/></svg></span>
      <div>
        <div class="phone-num">1-800-555-0142</div>
        <div class="phone-sub">Talk Today to a Local Advisor for FREE</div>
      </div>
    </div>
  </div>
</footer>
<div class="copyright">
  <span>COPYRIGHT © 2020 THE ELDER NOOK. ALL RIGHTS RESERVED.</span>
  <span class="social"><span></span><span></span><span></span></span>
</div>

</body>
</html>
```